Systems and Technology Consultants - Website

Design & Build a website for a new company which operates in the Systems and Technology space for Transportation, Government and Commercial sectors.

Overall design should be minimalist in nature.
Should also have a feed that provides news and event updates on the main page.
Logo has already been awarded and should be incorporated into the site.

We like the overall layout, functionality and simplicity of the below sites. Submitted designs could be similar to or a combination of the aspects on these sites, or perhaps a whole different concept - we are open to new ideas.
Norvique.com
Teblo.it

Update 1 Dated 27 May 2014

All I am moving away from the Teblo.it website and would like it to be more aligned with Norvique.com not only in layout but in functionality. I will be extending the deadline of this design brief for two weeks to incorporate additional requirements and will add addtional funding to the project.

Apologies for not having more information available to provide but with so many submissions its getting confusing.

Thanks Derek

Please note that the brief has been updated and the deadline has been extended.

Important: We will need two language versions of the website, English and Arabic; the website is hosted on HostPelican

Hello All, Thank you for your submissions. We have narrowed it down to the final 6 designers and I just wanted to take a moment and provide a bit of feedback regarding the concepts that we like and the modifications we are looking for. First, let me mention some of the design functions we like. - At the top of the homepage we really like the "region" or "language" tab so that the website can be viewed in both English and Arabic. - We like the homepage to have clear color variation so that the different sections of the homepage are distinct. Additionally, we like the bottom portion of the homepage to be in red. We feel that draws attention to our contact information. Again, we would like the colors to integrate black, gray-scale, red, etc. - Having a search tab at the top of the home page, or integrated into the main image, so that the site is easy to navigate. - We especially like the main image to have the scrolling tabs at the bottom so it is easy to browse the services offered (Consultancy, Solutions Architecture, Masters Systems Integration, Independent Design Review). - In regards to the services offered tab we really like the idea that a few people presented that have the outside of our logo with an icon in the middle of consultancy, solutions, etc., etc. Secondly, as mentioned in our brief we really enjoy the design of norvique site. Specially, we enjoy the strong iconic images they use, the way the tabs at the top scroll easily, and contact us page that generates an email. Lastly, I've included some photos of the concept we have been working on. What we are trying to demonstrate is how our company offers a range of services that are essentially linked together. We provide individual services that when combined present the full service package. We would like this concept to be integrated into the over concept of our website. Please feel free to ask for clarification of any of the above points or contact us if you have any additional questions. We appreciate all of your hard work and are very excited to see the updated designs. Best, Marta Vennick Quelbrant Senior Program Manager marta.vennick@quelbrant-example.com

Industry/Entity Type

Government

Font styles to use
Serif
Sans Serif

Requirements
Must have
• Must work on/adapt to various/mobile devices (responsive)
Must be simple and straightforward
Colors should be in line/matching with logo
2 language versions: English and Arabic (no Thai)
Services should be the first group/row of items after/below the main image
Note: the website will be hosted by hostpelican
Nice to have
• Submit feedback form
What's New section
The banner at the bottom of the site should not be too large; we would like a narrow one more
It would be nice if the header/top banner (with Home, About, etc. tabs) could stay in place as you scroll down (like Norvique and Chatterloop)
We will likely only use one image with a Company slogan on the Home page rather than a carousel of images to rotate through
Should not have
• This is the existing website: http://www.quelbrant-example.org
We do not like the animation, the way the banner icons/titles bounce
Not simple enough, we don't like the functionality or how pages load so slowly
We do not like the logo centered - it should be at the left
The banner and its tabs should not be towards the right, we would like them to be centered, to go all the way across and to be below the logo

```html
<!DOCTYPE html>
<html lang="en">
<head>
<meta charset="utf-8">
<title>Quelbrant — Systems and Technology Consultants</title>
<link href="https://fonts.googleapis.com/css2?family=Ubuntu:wght@300;400;500&family=Montserrat:wght@400;500&family=Open+Sans:wght@400;600&display=swap" rel="stylesheet">
<style>
:root{
  --red:#d3141b;
  --ink:#222;
  --text:#333;
  --muted:#888;
  --bar:#2b2b2b;
  --footer:#2e2e2e;
  --footer-deep:#232323;
  --line:#e4e4e4;
  --white:#fff;
}
*{margin:0;padding:0;box-sizing:border-box}
html,body{width:878px;height:1200px;overflow:hidden;background:var(--white)}
body{position:relative;font-family:"Open Sans",sans-serif;color:var(--text)}
.abs{position:absolute}

.topbar{left:0;top:0;width:878px;height:26px;background:var(--bar);color:#eee;font-size:9px}
.topbar .contact{left:82px;top:0;height:26px;display:flex;align-items:center;gap:16px}
.topbar .contact span{display:flex;align-items:center;gap:6px}
.topbar .social{right:82px;top:7px;display:flex;gap:9px}
.topbar .social i{display:block;width:11px;height:11px;border-radius:2px;background:#ddd}

.brand{left:82px;top:64px;width:120px;font-family:"Ubuntu",sans-serif;font-weight:500;font-size:20px;letter-spacing:1px;color:var(--red);white-space:nowrap}

.nav{top:70px;left:0;width:878px;font-family:"Ubuntu",sans-serif;font-size:11px;color:var(--ink)}
.nav a{position:absolute;top:0;color:inherit;text-decoration:none}
.nav a.active{color:var(--red);font-weight:500}
.nav a.active::after{content:"";position:absolute;left:-9px;right:-9px;top:20px;height:2px;background:var(--red)}

.hero{left:81px;top:129px;width:717px;height:385px;background:linear-gradient(90deg,#d9d9d9 0%,#f1f1f1 30%,#bdbdbd 60%,#8a8a8a 85%,#bcbcbc 100%)}
.hero-shadow{left:100px;top:514px;width:680px;height:16px;background:radial-gradient(ellipse at top,rgba(0,0,0,.22),rgba(0,0,0,0) 70%)}
.hero-figure{left:540px;top:175px;width:170px;height:339px;border-radius:80px 80px 0 0;background:linear-gradient(180deg,#5a5f66,#26282c)}
.hero-title{left:120px;top:245px;font-family:"Montserrat",sans-serif;font-size:18.5px;line-height:24px;color:#2b2b2b;font-weight:400;white-space:nowrap}
.hero-title b{color:var(--red);font-weight:500}
.cta{left:117px;top:335px;width:185px;height:31px;border-radius:16px;background:#1e1e1e;color:#fff;font-family:"Ubuntu",sans-serif;font-size:12px;display:flex;align-items:center;padding-left:12px}
.cta b{font-weight:500;margin-left:4px}
.cta .go{position:absolute;right:7px;top:6px;width:19px;height:19px;border-radius:50%;background:#fff}

.tile{top:563px;width:207px;height:62px;background:linear-gradient(180deg,#3a3a3a,#111);border-radius:4px;color:#fff;font-family:"Ubuntu",sans-serif}
.tile::after{content:"";position:absolute;left:8px;right:8px;bottom:-9px;height:8px;background:radial-gradient(ellipse at top,rgba(0,0,0,.25),rgba(0,0,0,0) 70%)}
.tile .icon{position:absolute;left:12px;top:15px;width:36px;height:32px}
.tile .rule{position:absolute;left:54px;top:14px;width:1px;height:34px;background:#555}
.tile h3{position:absolute;left:64px;top:17px;font-weight:400;font-size:16.5px;line-height:18px}
.tile p{position:absolute;left:64px;top:36px;font-size:9.5px}

.section-title{font-family:"Ubuntu",sans-serif;font-size:16.5px;color:var(--ink);font-weight:400}
.view-all{font-size:8px;color:var(--red)}
.heading-rule{height:1px;background:var(--line)}

.thumb{background:linear-gradient(135deg,#cfd6dc,#7d8894)}
.thumb.board{background:linear-gradient(135deg,#2f6aa0,#143a63)}
.item-title{font-family:"Ubuntu",sans-serif;font-size:12.5px;color:var(--text);font-weight:400}
.item-text{font-size:9.5px;line-height:14.5px;color:var(--muted)}
.read-more{width:70px;height:19px;border:1.5px solid var(--red);border-radius:3px;font-family:"Ubuntu",sans-serif;font-size:9.5px;color:var(--red);display:flex;align-items:center;justify-content:center}

.news .day{width:40px;text-align:center;font-family:"Ubuntu",sans-serif;font-size:20px;color:var(--red);font-weight:500;line-height:20px}
.news .mon{width:40px;text-align:center;font-family:"Ubuntu",sans-serif;font-size:17px;color:#222;line-height:20px}

.footer{left:0;top:946px;width:878px;height:200px;background:var(--footer);color:#ccc}
.footer-base{left:0;top:1146px;width:878px;height:54px;background:var(--footer-deep);color:#999;font-size:9.5px}
.f-head{font-family:"Ubuntu",sans-serif;font-size:11.5px;color:#eee;display:flex;align-items:center;gap:6px;font-weight:400;white-space:nowrap}
.f-head::after{content:"";display:block;height:3px;border-top:1px solid #555;border-bottom:1px solid #555;flex:1}
.f-list{font-size:8px;line-height:14.6px;color:#ccc;white-space:nowrap}
.f-list a{color:#ccc;text-decoration:underline}
.f-copy{font-size:8.5px;line-height:16px;color:#bbb}
.f-nav{font-size:8.5px;line-height:11.8px;color:#ddd}
.sq{width:24px;height:24px;border-radius:3px}
.newsletter{display:flex}
.newsletter .field{width:132px;height:22px;background:#262626;font-size:7.5px;font-style:italic;color:#777;display:flex;align-items:center;padding-left:9px}
.newsletter .btn{width:60px;height:22px;background:var(--red);color:#fff;font-family:"Ubuntu",sans-serif;font-size:10px;display:flex;align-items:center;justify-content:center}
.to-top{left:417px;top:1124px;width:44px;height:44px;border-radius:50%;background:#3a3a3a}
</style>
</head>
<body>

<header>
  <div class="abs topbar">
    <div class="abs contact">
      <span><svg width="8" height="10" viewBox="0 0 8 10"><rect x="1" y="0.5" width="6" height="9" rx="1" fill="none" stroke="#eee"/><rect x="2.5" y="2" width="3" height="4" fill="#eee"/></svg>0800-555-0142-6</span>
      <span><svg width="11" height="8" viewBox="0 0 11 8"><rect x="0.5" y="0.5" width="10" height="7" fill="none" stroke="#eee"/><path d="M0.5 0.5 L5.5 4.5 L10.5 0.5" fill="none" stroke="#eee"/></svg>contact@quelbrant-example.com</span>
    </div>
    <div class="abs social"><i></i><i></i><i></i><i></i><i></i><i></i></div>
  </div>

  <div class="abs brand">Quelbrant</div>

  <nav class="abs nav">
    <a class="active" style="left:336px">HOME</a>
    <a style="left:405px">Business Units</a>
    <a style="left:511px">Services</a>
    <a style="left:585px">About Us</a>
    <a style="left:664px">Locations</a>
    <a style="left:745px">Contact Us</a>
  </nav>
</header>

<section>
  <div class="abs hero" role="img" aria-label="Photo of a businessman in a suit standing before a grey city skyline with a digital world map overlay"></div>
  <div class="abs hero-figure" role="img" aria-label="Businessman figure"></div>
  <div class="abs hero-shadow"></div>
  <h1 class="abs hero-title"><b>Quelbrant</b> Specializes in delivering<br>Quality Professional Services and Techni-<br>cal Projects .</h1>
  <a class="abs cta">LEARN MORE <b>ABOUT US</b><span class="go"><svg width="19" height="19" viewBox="0 0 19 19"><path d="M5 9.5 H12 M9.5 6.5 L12.5 9.5 L9.5 12.5" stroke="#d3141b" stroke-width="2.2" fill="none"/></svg></span></a>
</section>

<section>
  <div class="abs tile" style="left:98px">
    <svg class="icon" viewBox="0 0 36 32"><circle cx="13" cy="9" r="6" fill="#fff"/><circle cx="24" cy="10" r="5" fill="#fff"/><path d="M2 28 Q3 17 13 17 Q23 17 24 28Z" fill="#fff"/><path d="M22 18 Q33 17 34 28 H26 Q26 21 22 18Z" fill="#fff"/></svg>
    <span class="rule"></span><h3>Mission Statement</h3><p>Lorem ipsum dolor sit</p>
  </div>
  <div class="abs tile" style="left:334px">
    <svg class="icon" viewBox="0 0 36 32"><circle cx="12" cy="12" r="7" fill="none" stroke="#fff" stroke-width="4" stroke-dasharray="3 2"/><circle cx="25" cy="22" r="6" fill="none" stroke="#fff" stroke-width="3.5" stroke-dasharray="3 2"/><circle cx="12" cy="12" r="2.5" fill="#fff"/><circle cx="25" cy="22" r="2" fill="#fff"/></svg>
    <span class="rule"></span><h3>Press Releases</h3><p>Lorem ipsum dolor sit</p>
  </div>
  <div class="abs tile" style="left:570px">
    <svg class="icon" viewBox="0 0 36 32"><path d="M4 24 L10 4 L20 14" fill="none" stroke="#fff" stroke-width="3"/><path d="M20 14 L22 20 H34 V25 H8Z" fill="#fff"/><rect x="7" y="26" width="27" height="5" rx="2.5" fill="none" stroke="#fff" stroke-width="1.5"/></svg>
    <span class="rule"></span><h3>Board of Directors</h3><p>Lorem ipsum dolor sit</p>
  </div>
</section>

<main>
  <section class="articles">
    <h2 class="abs section-title" style="left:84px;top:697px">Articles</h2>
    <a class="abs view-all" style="left:446px;top:705px">View All</a>
    <div class="abs heading-rule" style="left:82px;top:718px;width:396px"></div>

    <div class="abs thumb" style="left:83px;top:733px;width:142px;height:113px" role="img" aria-label="Photo of two business people in a meeting"></div>
    <h3 class="abs item-title" style="left:234px;top:731px">Lorem ipsum dolor sit amet, consectetur</h3>
    <p class="abs item-text" style="left:234px;top:753px;width:235px">Lorem Ipsum is simply dummy text of the printing and typesetting industry , when an unknown printer took a galley of type and scrambled it to make a type specimen book.</p>
    <a class="abs read-more" style="left:234px;top:822px">Read More</a>

    <div class="abs heading-rule" style="left:82px;top:856px;width:380px"></div>
    <div class="abs thumb board" style="left:83px;top:862px;width:88px;height:53px" role="img" aria-label="Photo of a blue circuit board"></div>
    <h3 class="abs item-title" style="left:184px;top:864px">Lorem ipsum dolor sit amet, consectetur</h3>
    <p class="abs item-text" style="left:184px;top:885px;width:250px">Lorem Ipsum is simply dummy text of the printing and typesetting industry...</p>
    <div class="abs heading-rule" style="left:82px;top:928px;width:380px"></div>
  </section>

  <div class="abs" style="left:500px;top:700px;width:1px;height:230px;background:linear-gradient(#fff,#e6e6e6,#fff)"></div>

  <section class="news">
    <h2 class="abs section-title" style="left:525px;top:697px">News</h2>
    <a class="abs view-all" style="left:754px;top:705px">View All</a>
    <div class="abs heading-rule" style="left:522px;top:718px;width:264px"></div>

    <div class="abs day" style="left:521px;top:737px">27</div><div class="abs mon" style="left:521px;top:758px">Feb</div>
    <h3 class="abs item-title" style="left:571px;top:733px">Lorem ipsum dolor sit amet,</h3>
    <p class="abs item-text" style="left:572px;top:755px;width:190px">Lorem Ipsum is simply dummy text of the printing and typesetting industry.</p>
    <div class="abs heading-rule" style="left:520px;top:792px;width:260px"></div>

    <div class="abs day" style="left:521px;top:803px">23</div><div class="abs mon" style="left:521px;top:824px">Feb</div>
    <h3 class="abs item-title" style="left:571px;top:800px">Lorem ipsum dolor sit amet,</h3>
    <p class="abs item-text" style="left:572px;top:821px;width:190px">Lorem Ipsum is simply dummy text of the printing and typesetting industry.</p>
    <div class="abs heading-rule" style="left:520px;top:860px;width:260px"></div>

    <div class="abs day" style="left:521px;top:871px">22</div><div class="abs mon" style="left:521px;top:892px">Feb</div>
    <h3 class="abs item-title" style="left:571px;top:869px">Lorem ipsum dolor sit amet,</h3>
    <p class="abs item-text" style="left:572px;top:889px;width:190px">Lorem Ipsum is simply dummy text of the printing and typesetting industry.</p>
    <div class="abs heading-rule" style="left:520px;top:928px;width:260px"></div>
  </section>
</main>

<footer>
  <div class="abs footer">
    <h4 class="abs f-head" style="left:94px;top:36px;width:114px">Contact Info</h4>
    <div class="abs f-list" style="left:95px;top:66px">
      <a>lorem ipsum</a><br><a>dolor sit amet 106</a><br><a>1404 consecteture</a><br><a>adipiscing elit</a><br><a>eMail: info@quelbrant-example.com</a><br><a>Phone: 1-800-555-0199</a>
    </div>

    <h4 class="abs f-head" style="left:245px;top:36px;width:154px">About Us</h4>
    <p class="abs f-copy" style="left:245px;top:66px;width:160px">Lorem ipsum dolor sit amet, consectetur adipisicing elit, sed do eiusmod tempor incididunt ut labore et dolore magna aliqua. Ut enim ad minim veniam.</p>

    <h4 class="abs f-head" style="left:434px;top:36px;width:114px">Company Info</h4>
    <div class="abs f-nav" style="left:437px;top:66px">Home<br>Business Units<br>Services<br>About Us<br>Locations<br>Contact Us</div>

    <h4 class="abs f-head" style="left:585px;top:36px;width:194px">Stay updates on our Socail Network</h4>
    <div class="abs" style="left:585px;top:69px;display:flex;gap:9px">
      <span class="sq" style="background:#3b5a99"></span><span class="sq" style="background:#4ab3e6"></span><span class="sq" style="background:#1b77b3"></span>
    </div>
    <h4 class="abs f-head" style="left:585px;top:109px;width:194px">Join Our Newsletter</h4>
    <div class="abs newsletter" style="left:585px;top:134px"><span class="field">Enter your email address</span><span class="btn">Subscribe</span></div>
  </div>
  <div class="abs footer-base">
    <span class="abs" style="left:97px;top:21px">© Copyrights 2014 All rights Reserved</span>
    <span class="abs" style="right:99px;top:21px">Privacy Policy &amp; Terms of uses</span>
  </div>
  <a class="abs to-top"><svg width="44" height="44" viewBox="0 0 44 44"><path d="M16 25 L22 19 L28 25" stroke="#666" stroke-width="2" fill="none"/></svg></a>
</footer>

</body>
</html>
```